Design a business card
Business name: Harbourline Growth Advisory
Improving Business Profitibility

- An Overview of the Business & Service:

Business Performance Consulting

- The Target Market: Small to medium-sized business

- Design Specifics:
White card, blue ink, moon eclipse

No Logo

Target Market(s)

Small to medium-sized business

Font styles to use
Sans Serif

```html
<!DOCTYPE html>
<html lang="en">
<head>
<meta charset="utf-8">
<title>Harbourline Growth Advisory – Business Card</title>
<link rel="stylesheet" href="https://fonts.googleapis.com/css2?family=Oswald:wght@500;600&family=Arimo:wght@400&family=Open+Sans:wght@400&display=swap">
<style>
  :root {
    --ink-blue: #0b4a91;
    --card-white: #f7f7f7;
    --page-bg: #e6e6e6;
    --text-light: #ffffff;
    --text-dark: #2b2b2b;
  }
  * { box-sizing: border-box; margin: 0; padding: 0; }
  html, body {
    width: 1200px; height: 900px; overflow: hidden;
    background: var(--page-bg);
  }
  .business-card {
    position: absolute; left: 150px; top: 171px;
    width: 900px; height: 558px;
    display: flex;
    background: var(--card-white);
    box-shadow: 0 6px 24px rgba(0,0,0,0.12);
  }
  .contact-panel {
    width: 425px; height: 100%;
    background: var(--ink-blue);
    color: var(--text-light);
    padding: 92px 39px 0 0;
    text-align: right;
    font-family: "Arimo", Arial, sans-serif;
  }
  .person-name {
    font-family: "Oswald", "Arial Narrow", sans-serif;
    font-weight: 500;
    font-size: 31px; line-height: 1.1;
    text-transform: uppercase;
    letter-spacing: 0.2px;
  }
  .person-title { font-size: 24px; line-height: 1.2; }
  .contact-list { list-style: none; margin-top: 96px; }
  .contact-item {
    font-size: 22px; line-height: 33px;
    display: flex; justify-content: flex-end; align-items: center; gap: 6px;
  }
  .contact-icon { width: 20px; height: 20px; fill: var(--text-light); flex: none; }
  .postal-address {
    font-style: normal; font-size: 23px; line-height: 33px; margin-top: 18px;
  }
  .brand-panel {
    flex: 1; position: relative;
    display: flex; flex-direction: column; align-items: center;
  }
  .brand-mark {
    width: 150px; height: 150px; margin-top: 100px;
    border-radius: 50%; background: var(--ink-blue);
  }
  .brand-name {
    margin-top: 38px;
    font-family: "Oswald", "Arial Narrow", sans-serif;
    font-weight: 600; font-size: 34px; line-height: 1.1;
    color: var(--ink-blue); text-transform: uppercase; text-align: center;
  }
  .brand-tagline {
    position: absolute; left: 0; right: 0; top: 445px;
    text-align: center;
    font-family: "Open Sans", Arial, sans-serif;
    font-size: 22px; color: var(--text-dark); text-transform: uppercase;
  }
</style>
</head>
<body>
  <article class="business-card">
    <section class="contact-panel">
      <h1 class="person-name">Desmond R Akerly</h1>
      <p class="person-title">Managing Director</p>
      <ul class="contact-list">
        <li class="contact-item">044-555 010 274
          <svg class="contact-icon" viewBox="0 0 24 24" aria-hidden="true"><path d="M3 9c0-3 4-5 9-5s9 2 9 5v2h-5V9H8v2H3z M6 12h12l2 8H4z"/></svg></li>
        <li class="contact-item">044-555 010 274
          <svg class="contact-icon" viewBox="0 0 24 24" aria-hidden="true"><path d="M7 2h10a1 1 0 0 1 1 1v18a1 1 0 0 1-1 1H7a1 1 0 0 1-1-1V3a1 1 0 0 1 1-1zm1 3v12h8V5zm4 13.5a1 1 0 1 0 0 2 1 1 0 0 0 0-2z" fill-rule="evenodd"/></svg></li>
        <li class="contact-item">info@harbourlinegrowth.com
          <svg class="contact-icon" viewBox="0 0 24 24" aria-hidden="true"><path d="M2 5h20v14H2z M3 6l9 7 9-7" fill="none" stroke="#fff" stroke-width="2"/><path d="M2 5h20v14H2z" opacity="0.9"/><path d="M3 6l9 7 9-7" fill="none" stroke="#0b4a91" stroke-width="2"/></svg></li>
        <li class="contact-item">www.harbourlinegrowth.com
          <svg class="contact-icon" viewBox="0 0 24 24" aria-hidden="true"><circle cx="12" cy="12" r="10"/><path d="M2 12h20M12 2c3 3 3 17 0 20M12 2c-3 3-3 17 0 20" fill="none" stroke="#0b4a91" stroke-width="1.5"/></svg></li>
      </ul>
      <address class="postal-address">48 Quayside Lane<br>Brightmoor, 204170</address>
    </section>
    <section class="brand-panel">
      <div class="brand-mark" aria-hidden="true"></div>
      <p class="brand-name">Harbourline<br>Growth Advisory</p>
      <p class="brand-tagline">Improving Business Profitibility</p>
    </section>
  </article>
</body>
</html>
```